Orvane Mechanical - Letterhead

We are a plumbing and hvac company based in Calgary. This letterhead will be on our quotes, invoices, preventative maintenance proposals etc.

```html
<!DOCTYPE html>
<html lang="en">
<head>
<meta charset="utf-8">
<title>Orvane Mechanical – Letterhead</title>
<link href="https://fonts.googleapis.com/css2?family=Open+Sans:wght@400;600;700&family=Roboto:wght@400&display=swap" rel="stylesheet">
<style>
  :root {
    --brand-blue: #1a6fbd;
    --brand-orange: #ea5424;
    --ink: #3a3a3a;
    --ink-soft: #555555;
    --paper-top: #ffffff;
    --paper-bottom: #f1f1f1;
    --backdrop: #e6e6e6;
  }
  * { box-sizing: border-box; margin: 0; padding: 0; }
  html, body {
    width: 1063px; height: 1200px; overflow: hidden;
    background: var(--backdrop);
  }
  .letterhead {
    position: relative;
    width: 1063px; height: 1200px;
    background: linear-gradient(180deg, var(--paper-top) 45%, var(--paper-bottom) 100%);
    font-family: "Open Sans", sans-serif;
    color: var(--ink);
    overflow: hidden;
  }
  .brand {
    position: absolute; top: 110px; left: 0; right: 0;
    display: flex; align-items: center; justify-content: center; gap: 14px;
  }
  .brand__dot {
    width: 32px; height: 32px; border-radius: 50%;
    background: var(--brand-orange);
  }
  .brand__name {
    font-weight: 700; font-size: 36px; letter-spacing: 0.5px;
    color: var(--brand-blue);
  }
  .letter {
    position: absolute; top: 270px; left: 165px; width: 740px;
    font-size: 14.5px; line-height: 22px; letter-spacing: 0.4px;
    color: var(--ink-soft);
  }
  .letter__salutation { margin-bottom: 18px; }
  .letter__para { margin-bottom: 22px; }
  .letter__closing { margin-top: 30px; }
  .signature {
    display: block; margin-top: 20px;
    width: 130px; height: 80px;
    background: linear-gradient(135deg, #f3f3f3, #e4e4e4);
    border-radius: 4px;
  }
  .contact {
    position: absolute; left: 0; right: 0; bottom: 56px;
    text-align: center;
    font-family: "Roboto", sans-serif;
    font-size: 20px; line-height: 30px; color: #2e2e2e;
  }
  .contact__row { display: flex; justify-content: center; align-items: center; gap: 12px; }
  .contact__item { display: inline-flex; align-items: center; gap: 7px; }
  .contact__icon { width: 17px; height: 17px; fill: var(--brand-orange); }
  .band {
    position: absolute; left: 0; bottom: 0; width: 1063px; height: 28px;
  }
</style>
</head>
<body>
<main class="letterhead">
  <header class="brand">
    <span class="brand__dot"></span>
    <span class="brand__name">Orvane Mechanical</span>
  </header>

  <section class="letter">
    <p class="letter__salutation">Dear customer,</p>
    <p class="letter__para">Lorem ipsum dolor sit amet, consectetur adipisicing elit, sed do eiusmod tempor incididunt ut labore et dolore magna aliqua. Ut enim ad minim veniam, quis nostrud exercitation ullamco laboris nisi ut aliquip ex ea commodo consequat. Duis aute irure dolor in reprehenderit in voluptate velit esse cillum dolore eu fugiat nulla pariatur. Excepteur sint occaecat cupidatat non proident, sunt in culpa qui officia deserunt mollit anim id est laborum.</p>
    <p class="letter__para">Lorem ipsum dolor sit amet, consectetur adipisicing elit, sed do eiusmod tempor incididunt ut labore et dolore magna aliqua. Ut enim ad minim veniam, quis nostrud exercitation ullamco laboris nisi ut aliquip ex ea commodo consequat. Duis aute irure dolor in reprehenderit in voluptate velit esse cillum dolore eu fugiat nulla pariatur. Excepteur sint occaecat cupidatat non proident, sunt in culpa qui officia deserunt mollit anim id est laborum.</p>
    <p class="letter__para">Lorem ipsum dolor sit amet, consectetur adipisicing elit, sed do eiusmod tempor incididunt ut labore et dolore magna aliqua. Ut enim ad minim veniam, quis nostrud exercitation ullamco laboris nisi ut aliquip ex ea commodo consequat. Duis aute irure dolor in reprehenderit in voluptate velit esse cillum dolore eu fugiat nulla pariatur. Excepteur sint occaecat cupidatat non proident, sunt in culpa qui officia deserunt mollit anim id est laborum.</p>
    <p class="letter__para">Lorem ipsum dolor sit amet, consectetur adipisicing elit, sed do eiusmod tempor incididunt ut labore et dolore magna aliqua. Ut enim ad minim veniam, quis nostrud exercitation ullamco laboris nisi ut aliquip ex ea commodo consequat. Duis aute irure dolor in reprehenderit.</p>
    <p class="letter__closing">Yours Sincerely,</p>
    <span class="signature" role="img" aria-label="Handwritten signature"></span>
  </section>

  <footer class="contact">
    <p>1820 Bowmont Crescent NW, Suite 210 Calgary.</p>
    <p class="contact__row">
      <span class="contact__item">
        <svg class="contact__icon" viewBox="0 0 24 24" aria-hidden="true"><path d="M6.6 10.8a15.1 15.1 0 0 0 6.6 6.6l2.2-2.2a1 1 0 0 1 1-.25 11.4 11.4 0 0 0 3.6.57 1 1 0 0 1 1 1V20a1 1 0 0 1-1 1A17 17 0 0 1 3 4a1 1 0 0 1 1-1h3.5a1 1 0 0 1 1 1c0 1.25.2 2.45.57 3.57a1 1 0 0 1-.25 1z"/></svg>
        403.555.0147
      </span>
      <span class="contact__item">
        <svg class="contact__icon" viewBox="0 0 24 24" aria-hidden="true"><path d="M2 5h20v14H2z" fill="none" stroke="var(--brand-orange)" stroke-width="2"/><path d="M2 5l10 8 10-8" fill="none" stroke="var(--brand-orange)" stroke-width="2"/></svg>
        info@orvanemech.com
      </span>
      <span class="contact__item">
        <svg class="contact__icon" viewBox="0 0 24 24" aria-hidden="true"><circle cx="12" cy="12" r="10"/></svg>
        www.orvanemech.com
      </span>
    </p>
  </footer>

  <svg class="band" viewBox="0 0 1063 28" preserveAspectRatio="none" aria-hidden="true">
    <polygon points="0,0 520,0 548,28 0,28" fill="var(--brand-blue)"/>
    <polygon points="532,0 1063,0 1063,28 560,28" fill="var(--brand-orange)"/>
  </svg>
</main>
</body>
</html>
```